Automotive Accessories Business Card

Design a business template that match our new logo design and our industry.

https://www.qelmotorgear.com/

Target Market(s)

Aftermarket auto parts and accessories

Industry/Entity Type

automotive

Contact Information for Business Card

company logo

Font styles to use
Serif
Sans Serif

Colors
EB3D1F
EC4F4E
F09395
F8D3D4
FCEDEE

```html
<!DOCTYPE html>
<html lang="en">
<head>
<meta charset="utf-8">
<title>QEL Motor Gear – Business Card</title>
<link rel="stylesheet" href="https://fonts.googleapis.com/css2?family=Poppins:wght@400;500;700;800&display=swap">
<style>
  :root {
    --bg: #2a2a2b;
    --card: #1c1d1f;
    --card-edge: #141516;
    --red: #e0262b;
    --white: #ffffff;
    --rule: #6b6b6e;
    --pattern-dark: #111213;
    --pattern-light: #3c3d40;
  }
  * { box-sizing: border-box; margin: 0; padding: 0; }
  html, body { width: 1200px; height: 1108px; overflow: hidden; }
  body {
    background: var(--bg);
    font-family: "Poppins", sans-serif;
    color: var(--white);
    position: relative;
  }
  .card {
    position: absolute;
    top: 224px;
    width: 400px;
    height: 660px;
    border-radius: 22px;
    background: var(--card);
    overflow: hidden;
  }
  .card--front { left: 160px; }
  .card--back { left: 640px; }

  /* Front */
  .brand {
    position: absolute;
    top: 120px;
    left: 0; right: 0;
    display: flex;
    align-items: center;
    justify-content: center;
    gap: 12px;
  }
  .brand__mark { width: 22px; height: 22px; background: var(--red); }
  .brand__name {
    font-weight: 800;
    font-size: 30px;
    letter-spacing: 1px;
    color: var(--white);
  }
  .person {
    position: absolute;
    top: 300px;
    left: 0; right: 0;
    text-align: center;
  }
  .person__name {
    color: var(--red);
    font-weight: 700;
    font-size: 27px;
    letter-spacing: 0.5px;
    text-transform: uppercase;
    line-height: 1.1;
  }
  .person__title { font-size: 17px; font-weight: 400; margin-top: 2px; }
  .icon-row {
    position: absolute;
    top: 384px;
    left: 50px; right: 50px;
    display: flex;
    align-items: center;
    gap: 8px;
  }
  .icon-row__rule { flex: 1; height: 1px; background: var(--rule); }
  .icon {
    width: 26px; height: 26px;
    background: var(--red);
    border-radius: 4px;
    display: flex; align-items: center; justify-content: center;
  }
  .icon svg { width: 16px; height: 16px; }
  .contacts {
    position: absolute;
    top: 424px;
    left: 0; right: 0;
    text-align: center;
    font-size: 17px;
    line-height: 1.42;
  }
  .divider {
    position: absolute;
    top: 514px;
    left: 70px; right: 70px;
    height: 1px;
    background: var(--rule);
  }
  .address {
    position: absolute;
    top: 530px;
    left: 0; right: 0;
    text-align: center;
    font-size: 17px;
    line-height: 1.42;
  }

  /* Back */
  .pattern {
    position: absolute;
    inset: 0;
    background: linear-gradient(200deg, var(--pattern-light) 0%, var(--pattern-dark) 70%);
  }
  .back-brand {
    position: absolute;
    top: 50%;
    left: 0; right: 0;
    transform: translateY(-50%);
    text-align: center;
    font-weight: 800;
    font-size: 30px;
    letter-spacing: 1px;
    color: var(--white);
  }
</style>
</head>
<body>
  <section class="card card--front" aria-label="Business card front">
    <div class="brand">
      <span class="brand__mark"></span>
      <span class="brand__name">QEL MOTOR GEAR</span>
    </div>

    <div class="person">
      <p class="person__name">Marcus Hale</p>
      <p class="person__title">Managing Director</p>
    </div>

    <div class="icon-row">
      <span class="icon-row__rule"></span>
      <span class="icon" aria-label="Phone">
        <svg viewBox="0 0 16 16"><path d="M4 1.5 6 4 5 5.6c.8 1.8 2.1 3.1 3.9 4L10.5 8.5 13 10.5 12 13c-5 0-9-4-9.5-9z" fill="none" stroke="#fff" stroke-width="1.3" stroke-linejoin="round"/></svg>
      </span>
      <span class="icon" aria-label="Email">
        <svg viewBox="0 0 16 16"><rect x="2" y="4" width="12" height="8.5" fill="none" stroke="#fff" stroke-width="1.3"/><path d="M2 4l6 5 6-5" fill="none" stroke="#fff" stroke-width="1.3"/></svg>
      </span>
      <span class="icon" aria-label="Website">
        <svg viewBox="0 0 16 16"><circle cx="8" cy="8" r="6" fill="none" stroke="#fff" stroke-width="1.3"/><ellipse cx="8" cy="8" rx="2.6" ry="6" fill="none" stroke="#fff" stroke-width="1.1"/><path d="M2 8h12" stroke="#fff" stroke-width="1.1"/></svg>
      </span>
      <span class="icon-row__rule"></span>
    </div>

    <div class="contacts">
      <p>044-555 010 234</p>
      <p>info@qelmotorgear.com</p>
      <p>www.qelmotorgear.com</p>
    </div>

    <div class="divider"></div>

    <div class="address">
      <p>421, Address line goes here</p>
      <p>45452,Country Name</p>
    </div>
  </section>

  <section class="card card--back" aria-label="Business card back">
    <div class="pattern" role="img" aria-label="Repeating embossed brand name pattern in dark grey gloss"></div>
    <p class="back-brand">QEL MOTOR GEAR</p>
  </section>
</body>
</html>
```